Meridale Bed Company Needs Business Card

Looking for a very nice looking business card. Creative but not extravagant. We sell beds and pillows across the U.S. and need something professional but catchy. I have attached the logo.

Name : Devin Holt
Title : President
Phone : (800) 471-2960
Email: sleep@quilmora.com
Website: www.quilmora.com

Can be single-sided or double-sided
horizontal or vertical

Can use Blues/Greys

Target Market(s)

Mass Market

Industry/Entity Type

Retail

Contact Information for Business Card

Name : Devin Holt
Title : President
Phone : (800) 471-2960
Email: sleep@quilmora.com
Website: www.quilmora.com

Requirements
Must have
• Clean, Modern, Smooth
• Can use Blues/Greys
• On the other side without the information - have something simple like www.quilmora.com or our logo
Nice to have
• Surprise me
Should not have
• Nothing crazy, nothing cluttered

```html
<!DOCTYPE html>
<html lang="en">
<head>
<meta charset="utf-8">
<title>Meridale Bed Company – Business Card</title>
<link href="https://fonts.googleapis.com/css2?family=Montserrat:wght@400;500&family=Quicksand:wght@400;500;600&display=swap" rel="stylesheet">
<style>
  :root {
    --blue: #29a8e0;
    --grey: #a3a3a3;
    --text-grey: #6f6f6f;
    --card: #ffffff;
    --backdrop: #dcdcde;
  }
  * { margin: 0; padding: 0; box-sizing: border-box; }
  html, body { width: 1200px; height: 858px; overflow: hidden; }
  body { background: var(--backdrop); position: relative; }

  .card {
    position: absolute;
    top: 158px;
    width: 310px;
    height: 542px;
    background: var(--card);
    overflow: hidden;
    box-shadow: 0 6px 22px rgba(0,0,0,0.12);
  }
  .card--front { left: 255px; }
  .card--back { left: 635px; }

  .brand {
    font-family: "Quicksand", sans-serif;
    font-weight: 400;
    color: var(--blue);
    letter-spacing: 1px;
  }
  .card--front .brand {
    position: absolute;
    top: 220px;
    left: 0;
    width: 100%;
    text-align: center;
    font-size: 56px;
  }
  .card--back .brand {
    position: absolute;
    top: 34px;
    left: 0;
    width: 100%;
    text-align: center;
    font-size: 48px;
  }

  .front-web {
    position: absolute;
    left: 44px;
    bottom: 66px;
    display: flex;
    align-items: center;
    gap: 10px;
    font-family: "Montserrat", sans-serif;
    font-size: 18px;
    letter-spacing: 1px;
    color: var(--text-grey);
  }
  .icon-tile {
    width: 20px; height: 20px;
    border-radius: 4px;
    background: var(--blue);
    display: flex; align-items: center; justify-content: center;
  }

  .base-band { position: absolute; left: 0; bottom: 0; width: 310px; height: 48px; display: block; }

  .person {
    position: absolute;
    top: 196px;
    right: 0;
    display: flex;
    align-items: stretch;
    gap: 10px;
  }
  .person__text { text-align: right; padding-top: 12px; }
  .person__name {
    font-family: "Quicksand", sans-serif;
    font-weight: 600;
    font-size: 25px;
    color: var(--text-grey);
    line-height: 1;
  }
  .person__title {
    font-family: "Quicksand", sans-serif;
    font-weight: 600;
    font-size: 19px;
    color: var(--blue);
    margin-top: 2px;
  }
  .person__bar { width: 18px; height: 82px; background: var(--blue); }

  .contact {
    position: absolute;
    top: 382px;
    left: 0;
    width: 280px;
    display: flex;
  }
  .contact__strip {
    width: 30px;
    background: var(--blue);
    display: flex;
    flex-direction: column;
    justify-content: space-around;
    align-items: center;
    padding: 14px 0 8px;
  }
  .contact__list { list-style: none; flex: 1; padding-left: 12px; }
  .contact__item {
    font-family: "Montserrat", sans-serif;
    font-size: 16px;
    color: var(--text-grey);
    padding: 12px 0 5px;
    border-bottom: 1px solid var(--blue);
  }
  .contact__item:last-child { border-bottom: none; }
</style>
</head>
<body>

<section class="card card--front" aria-label="Business card front">
  <div class="brand">quilmora</div>
  <div class="front-web">
    <span class="icon-tile">
      <svg width="14" height="14" viewBox="0 0 14 14" fill="none" stroke="#fff" stroke-width="1.1">
        <circle cx="7" cy="7" r="5.5"/><ellipse cx="7" cy="7" rx="2.4" ry="5.5"/>
        <line x1="1.5" y1="7" x2="12.5" y2="7"/><line x1="2.4" y1="4.2" x2="11.6" y2="4.2"/><line x1="2.4" y1="9.8" x2="11.6" y2="9.8"/>
      </svg>
    </span>
    <span>www.quilmora.com</span>
  </div>
  <svg class="base-band" viewBox="0 0 310 48" aria-hidden="true">
    <polygon points="0,22 112,22 100,48 0,48" fill="var(--grey)"/>
    <polygon points="128,0 310,0 310,48 108,48" fill="var(--blue)"/>
  </svg>
</section>

<section class="card card--back" aria-label="Business card back">
  <div class="brand">quilmora</div>

  <div class="person">
    <div class="person__text">
      <div class="person__name">Devin Holt</div>
      <div class="person__title">President</div>
    </div>
    <div class="person__bar"></div>
  </div>

  <div class="contact">
    <div class="contact__strip">
      <span class="icon-tile" style="background:#fff">
        <svg width="14" height="14" viewBox="0 0 24 24"><path fill="var(--blue)" d="M6.6 10.8a15 15 0 0 0 6.6 6.6l2.2-2.2a1 1 0 0 1 1-.25 11.4 11.4 0 0 0 3.6.57 1 1 0 0 1 1 1V20a1 1 0 0 1-1 1A17 17 0 0 1 3 4a1 1 0 0 1 1-1h3.5a1 1 0 0 1 1 1c0 1.25.2 2.45.57 3.57a1 1 0 0 1-.25 1z"/></svg>
      </span>
      <span class="icon-tile" style="background:#fff">
        <svg width="14" height="14" viewBox="0 0 14 14" fill="none" stroke="var(--blue)" stroke-width="1.3"><rect x="1.5" y="3" width="11" height="8"/><polyline points="1.5,3 7,8 12.5,3"/></svg>
      </span>
      <span class="icon-tile" style="background:#fff">
        <svg width="14" height="14" viewBox="0 0 14 14" fill="none" stroke="var(--blue)" stroke-width="1.1">
          <circle cx="7" cy="7" r="5.5"/><ellipse cx="7" cy="7" rx="2.4" ry="5.5"/><line x1="1.5" y1="7" x2="12.5" y2="7"/>
        </svg>
      </span>
    </div>
    <ul class="contact__list">
      <li class="contact__item">(800) 471-2960</li>
      <li class="contact__item">sleep@quilmora.com</li>
      <li class="contact__item">www.quilmora.com</li>
    </ul>
  </div>

  <svg class="base-band" viewBox="0 0 310 48" aria-hidden="true">
    <polygon points="0,22 112,22 100,48 0,48" fill="var(--grey)"/>
    <polygon points="128,0 310,0 310,48 108,48" fill="var(--blue)"/>
  </svg>
</section>

</body>
</html>
```